Quirky Label Design for an Exciting UK-Based Organic Skincare Company!

We need label designs across our range of products, we are a high quality yet quirky organic skincare company called Simply Cordell, we use frosted glass packaging, and we are just wanting one design done for now, but the winning designer we would want to work with to design the rest of the labels for us. We also want them to design business cards and other literature at some point and maybe even a website page.

Our label design will go on a 63mm tall frosted glass jar which is 62mm in diameter. The actual label dimensions should be, 170 mm (W) x 50 mm (H). The idea is so that it wraps around the whole jar with the design at one side (at the front) and the ingredients on another (at the back).

LABEL 1
Organic Polynesian Whipped Body Butter
Vanilla Bean
120ml

Made with Organic Shea and Cocoa Butters and exotic Monoi de Tahiti

Ingredients (INCI): Organic Raw Shea Butter (Butyrospermum Parkii), Organic Raw Cocoa Butter (Theobroma Cacao), Monoi de Tahiti (Coconut (Cocos nucifera) oil (and) Tiare (Gardenia tahitensis) flower), Organic Sweet Almond Oil (Prunus Amygdalus Dulcis), Organic Madagascan Vanilla Extract (Vanillin)

Handmade by Simply Cordell Ltd
14 Fernwick Lane, Bournemouth BH4 9QT, UK
Batch:

OPTIONAL WRITING (if it fits in):
100% Natural and Organic
Intensely Moisturising

LABEL 2
Mango Smoothie
120ml

Ingredients (INCI): Organic Raw Shea Butter (Butyrospermum Parkii), Organic Raw Cocoa Butter (Theobroma Cacao), Monoi de Tahiti (Coconut (Cocos nucifera) oil (and) Tiare (Gardenia tahitensis) flower), Organic Sweet Almond Oil (Prunus Amygdalus Dulcis), Organic Mango Flavour (Aroma)

Batch:

100% Natural and Organic
Intensely Moisturising

I have attached a picture of the jar we use and the lid we use for these products, as well as our logo. I've also attached a 'Handmade in Dorset' stamp which we'd like to go on there if possible, along with a shelf life symbol.

I am thinking the background colour of the labels will be either white or even brown paper colour. Perhaps it would be interesting to see it in both. UPDATE: We have decided on white background now, not brown.

The final design should denote handmade, organic, high quality, pure, yet quirky and original / unique. I am thinking perhaps a seemingly hand-drawn black leaf outline? Could fit the bill, but as I say, up to you. Something that says handmade yet professional.

I'd like to have the original Photoshop files from the winning designer so we can use them as a template for the rest of our horizontal labels.
Updates

Project Deadline Extended
Reason: Just need a few more days for designs we like to be worked on further, and to review new designs!

Target Market(s)

Everyone that appreciates a good quality skincare product focusing on natural & organic. Price is mid-range to high

Industry/Entity Type

It Company

Requirements
Must have
• Must make the product look high quality & organic yet quirky and accessible. Must have our logo and the shelf life symbol and the writing as above.
Nice to have
• Nice to have the 'handmade' stamp attached, but not absolutely necessary if it doesn't fit within your design.

```html
<!DOCTYPE html>
<html lang="en">
<head>
<meta charset="utf-8">
<title>Simply Cordell – Whipped Body Butter Label</title>
<link rel="stylesheet" href="https://fonts.googleapis.com/css2?family=Cinzel:wght@400;500&family=Mulish:wght@400;600;800&display=swap">
<style>
  :root {
    --page-bg: #f3f1ea;
    --paper-light: #f6f0d2;
    --paper-mid: #efe4b6;
    --paper-deep: #e6d89f;
    --ink: #2a2622;
    --ink-soft: #3b3632;
    --rose: #d2777a;
    --maroon: #7a2431;
    --silver-light: #f4f4f4;
    --silver-mid: #c9c9c9;
    --silver-dark: #8d8d8d;
    --badge-brown: #6e4a3a;
  }
  * { box-sizing: border-box; margin: 0; padding: 0; }
  html, body { width: 1200px; height: 663px; overflow: hidden; background: var(--page-bg); }
  body { font-family: "Mulish", sans-serif; color: var(--ink); }

  .canvas { position: relative; width: 1200px; height: 663px; }

  .label {
    position: absolute; left: 30px; top: 163px;
    width: 1140px; height: 336px;
    overflow: hidden;
    box-shadow: 0 6px 18px rgba(0,0,0,.12);
  }
  .label__paper {
    position: absolute; inset: 0;
    background: linear-gradient(100deg, var(--paper-deep) 0%, var(--paper-light) 22%, var(--paper-mid) 45%, var(--paper-light) 60%, var(--paper-mid) 80%, var(--paper-deep) 100%);
  }
  .label__swoosh { position: absolute; left: 0; bottom: 0; width: 1140px; height: 60px; }

  .panel { position: absolute; top: 0; height: 100%; }
  .panel--back { left: 0; width: 380px; padding: 22px 62px 0 18px; }
  .panel--front { left: 380px; width: 380px; text-align: center; }
  .panel--side { left: 760px; width: 380px; text-align: center; padding-top: 20px; }

  .ingredients__title { font-weight: 800; font-size: 14.5px; margin-bottom: 10px; }
  .ingredients__text { font-size: 14.5px; line-height: 21px; text-align: justify; hyphens: auto; color: var(--ink-soft); }

  .claims { display: flex; align-items: center; gap: 12px; margin-top: 16px; }
  .claims__badge { width: 62px; height: 62px; border-radius: 50%; border: 3px solid var(--badge-brown); background: rgba(110,74,58,.15); flex: none; }
  .claims__text { font-weight: 800; font-size: 13.5px; line-height: 20px; color: var(--ink); }

  .front__decor {
    position: absolute; left: 100px; top: 6px; width: 180px; height: 160px; border-radius: 50%;
    background: radial-gradient(circle, rgba(255,255,255,.95) 0%, rgba(255,255,255,.85) 45%, rgba(230,170,165,.35) 70%, rgba(230,170,165,0) 100%);
  }
  .front__brand {
    position: absolute; left: 0; right: 0; top: 64px;
    font-weight: 800; font-size: 34px; line-height: 40px; color: var(--rose);
  }
  .front__kicker { position: absolute; left: 0; right: 0; top: 170px; font-family: "Cinzel", serif; font-weight: 400; font-size: 22px; line-height: 26px; letter-spacing: 1px; color: var(--ink); }
  .front__title { position: absolute; left: 0; right: 0; top: 197px; font-family: "Cinzel", serif; font-weight: 400; font-size: 28px; line-height: 34px; letter-spacing: .5px; color: var(--ink); }
  .front__variant {
    position: absolute; left: 40px; right: 40px; top: 238px; height: 30px;
    display: flex; align-items: center; justify-content: center;
  }
  .front__variant::before, .front__variant::after { content: ""; flex: 1; height: 1px; background: var(--silver-dark); }
  .front__variant-bar {
    padding: 2px 10px; margin: 0 8px;
    background: linear-gradient(180deg, var(--silver-light), var(--silver-mid) 55%, var(--silver-dark));
    font-family: "Mulish", sans-serif; font-size: 20px; line-height: 26px; letter-spacing: 6px; color: var(--ink);
  }
  .front__size {
    position: absolute; left: 145px; top: 280px; width: 90px; height: 56px; border-radius: 45px 45px 0 0;
    background: #fff;
  }
  .front__size-label { display: block; font-size: 12px; line-height: 14px; font-weight: 600; margin-top: 8px; }
  .front__size-value { display: block; font-size: 21px; font-weight: 600; line-height: 26px; }

  .stamp { width: 78px; height: 78px; margin: 0 auto; border-radius: 50%; border: 2px solid var(--ink); background: rgba(255,255,255,.55); }
  .side__made { margin-top: 14px; font-weight: 600; font-size: 14px; line-height: 19px; }
  .side__brand { margin-top: 16px; font-weight: 800; font-size: 20px; line-height: 24px; color: var(--maroon); }
  .side__maker { margin-top: 32px; font-weight: 800; font-size: 16px; line-height: 20px; color: var(--maroon); }
  .side__address { font-size: 14.5px; line-height: 19.5px; color: var(--ink); }
</style>
</head>
<body>
<main class="canvas">
  <section class="label">
    <div class="label__paper" role="img" aria-label="Cream paper background with faint hand-drawn leaf pattern"></div>
    <svg class="label__swoosh" viewBox="0 0 1140 60" preserveAspectRatio="none" aria-hidden="true">
      <defs>
        <linearGradient id="silver" x1="0" y1="0" x2="0" y2="1">
          <stop offset="0" stop-color="#ffffff"/>
          <stop offset=".5" stop-color="#d8d8d8"/>
          <stop offset="1" stop-color="#9b9b9b"/>
        </linearGradient>
      </defs>
      <path d="M0 22 C300 16 420 44 600 26 C780 8 900 38 1140 14 L1140 60 L0 60 Z" fill="url(#silver)"/>
      <path d="M0 32 C300 28 420 54 600 36 C780 20 900 48 1140 26 L1140 60 L0 60 Z" fill="#f7f7f7"/>
    </svg>

    <div class="panel panel--back">
      <h2 class="ingredients__title">Ingredients (INCI):</h2>
      <p class="ingredients__text" lang="en">Organic Raw Shea Butter (Butyrospermum Parkii), Organic Raw Cocoa Butter (Theobroma Cacao), Monoi de Tahiti (Coconut (Cocos nucifera) oil (and) Tiare (Gardenia tahitensis) flower), Organic Sweet Almond Oil (Prunus Amygdalus Dulcis), Organic Madagascan Vanilla Extract (Vanillin)</p>
      <div class="claims">
        <span class="claims__badge" role="img" aria-label="Natural products badge"></span>
        <p class="claims__text">100% Natural and Organic<br>Intensely Moisturising</p>
      </div>
    </div>

    <div class="panel panel--front">
      <div class="front__decor" role="img" aria-label="Soft floral wreath behind the brand name"></div>
      <p class="front__brand">Simply Cordell</p>
      <p class="front__kicker">Organic Polynesian</p>
      <h1 class="front__title">Whipped Body Butter</h1>
      <div class="front__variant"><span class="front__variant-bar">VANILLA BEAN</span></div>
      <div class="front__size">
        <span class="front__size-label">Net Wt.</span>
        <span class="front__size-value">120ml</span>
      </div>
    </div>

    <div class="panel panel--side">
      <div class="stamp" role="img" aria-label="Handmade stamp"></div>
      <p class="side__made">Made with<br>Organic Shea and Cocoa Butters<br>and exotic Monoi de Tahiti</p>
      <p class="side__brand">Simply Cordell</p>
      <p class="side__maker">Handmade by Simply Cordell Ltd</p>
      <p class="side__address">14 Fernwick Lane, Bournemouth<br>BH4 9QT, UK<br>Batch:</p>
    </div>
  </section>
</main>
</body>
</html>
```